New business card/stationary for a consulting company

I am looking for a clean and very professional looking business card for my consulting company as well as corresponding stationary. I am uploading our logo. I like simple and powerful for the feel. No graphics but I am open on everything else. Below is my contact information but would like the final to be in a version I can add my employees information into and print. Thank you.

Daniel Whitcombe
dan@ferncliffadvisory.com
2870 North 9th Avenue, Summit Floor, Elm Ridge, Illinois 60531
www.ferncliffadvisory.com

Industry/Entity Type

Consulting

Contact Information for Business Card

Daniel Whitcombe
dan@ferncliffadvisory.com
www.ferncliffadvisory.com

Font styles to use
Serif
Sans Serif

Requirements
Must have
• Our logo and the business card details.
Nice to have
• our website www.ferncliffadvisory.com

```html
<!DOCTYPE html>
<html lang="en">
<head>
<meta charset="utf-8">
<title>Ferncliff Advisory — Business Card</title>
<link rel="stylesheet" href="https://fonts.googleapis.com/css2?family=Marcellus&family=Roboto:wght@400&display=swap">
<style>
  :root {
    --backdrop: #d9d4ce;
    --card: #eef1f2;
    --card-edge: #cfd5d8;
    --band: #1f3566;
    --band-text: #ece4d6;
    --mark: #ece4d6;
    --name: #1f2d52;
    --body-text: #2a2c31;
  }
  * { margin: 0; padding: 0; box-sizing: border-box; }
  html, body {
    width: 1200px;
    height: 970px;
    overflow: hidden;
    background: var(--backdrop);
  }
  .card {
    position: absolute;
    left: 170px;
    top: 245px;
    width: 860px;
    height: 480px;
    background: var(--card);
    border: 1px solid var(--card-edge);
    border-radius: 4px;
    box-shadow: 0 10px 30px rgba(60, 50, 40, 0.18);
  }
  .brand-band {
    position: absolute;
    left: 0;
    top: 68px;
    width: 100%;
    height: 100px;
    background: var(--band);
    display: flex;
    align-items: center;
    justify-content: center;
    gap: 22px;
  }
  .brand-square {
    width: 46px;
    height: 46px;
    background: var(--mark);
  }
  .brand-name {
    font-family: "Marcellus", serif;
    font-size: 40px;
    letter-spacing: 2px;
    color: var(--band-text);
    line-height: 1;
  }
  .contact {
    position: absolute;
    left: 0;
    top: 222px;
    width: 100%;
    text-align: center;
    color: var(--body-text);
    font-family: "Roboto", sans-serif;
  }
  .contact-name {
    font-family: "Marcellus", serif;
    font-size: 27px;
    letter-spacing: 2px;
    color: var(--name);
    margin-bottom: 16px;
  }
  .contact-line {
    font-size: 19px;
    line-height: 31px;
  }
  .contact-address {
    margin-top: 12px;
    font-size: 19px;
    line-height: 31px;
  }
</style>
</head>
<body>
  <div class="card">
    <div class="brand-band">
      <div class="brand-square"></div>
      <div class="brand-name">FERNCLIFF ADVISORY</div>
    </div>
    <div class="contact">
      <p class="contact-name">DANIEL WHITCOMBE</p>
      <p class="contact-line">dan@ferncliffadvisory.com</p>
      <p class="contact-line">www.ferncliffadvisory.com</p>
      <p class="contact-address">2870 North 9th Avenue, Summit<br>Floor, Elm Ridge, Illinois 60531</p>
    </div>
  </div>
</body>
</html>
```